****Business Card Design for Quarrystone Development. Design based around attached logo/company name

I’m looking for business card design for my company Quarrystone Development Group,LLC. Design should be professional, sharp and minimal. Outside of the attached logos, greyscale colors for remainder of cards. My thoughts are two-sided card with attached logo on one side and my info on the other but open to one-sided as well with right design.
Target Market(s)
Real estate professionals including banks, private investors, property owners, developers, commercial tenants like Brewlantern, Grovika or Tanquist’s.
Industry/Entity Type
Commercial real estate development and investments.
Contact Information for Business Card
Name, title, email, phone #’s, web address and physical address
Font styles to use
Other font styles liked:
- Helvetica, Garamond, etc
Colors
Designer to choose only greyscale colors for use in the design.
Requirements
Must have
- Attached logo first or second options.
Nice to have
- Two sided card with logo on one side. Attached Logo/company name can be laid out any way that flows as long as it’s legible.name
Should not have
- No loud colors. ***Please do not include logo, I have removed the company design with a logo image.

```html
<!DOCTYPE html>
<html lang="en">
<head>
<meta charset="utf-8">
<title>Quarrystone Development Group, LLC – Business Cards</title>
<link rel="stylesheet" href="https://fonts.googleapis.com/css2?family=Cinzel:wght@700&family=Arimo:wght@400&display=swap">
<style>
  :root {
    --backdrop: #161616;
    --card: #333436;
    --ink-bright: #f2f2f2;
    --ink-soft: #d9d9d9;
    --ink-muted: #7a7c80;
  }
  * { margin: 0; padding: 0; box-sizing: border-box; }
  html, body {
    width: 1200px; height: 852px; overflow: hidden;
    background: var(--backdrop);
  }
  .canvas {
    position: relative; width: 1200px; height: 852px;
    display: flex; flex-direction: column; align-items: center; justify-content: center; gap: 40px;
  }
  .card {
    position: relative; width: 630px; height: 360px;
    background: var(--card);
    box-shadow: 0 12px 30px rgba(0,0,0,.55);
  }
  .company-name {
    font-family: "Arimo", sans-serif; font-weight: 400;
    color: var(--ink-bright); line-height: 1.3;
  }
  .card--front .company-name {
    position: absolute; left: 0; right: 0; top: 50%; transform: translateY(-50%);
    text-align: center; font-size: 30px;
  }
  .card--back .company-name {
    position: absolute; left: 58px; top: 58px; font-size: 20px;
  }
  .person { position: absolute; left: 58px; top: 172px; font-family: "Arimo", sans-serif; }
  .person__name {
    font-family: "Cinzel", serif; font-weight: 700; font-size: 20px;
    letter-spacing: .14em; color: var(--ink-bright);
  }
  .person__title { font-size: 15px; color: var(--ink-soft); margin-top: 2px; }
  .details { margin-top: 22px; font-size: 15px; line-height: 1.35; color: var(--ink-soft); }
  .details__group + .details__group { margin-top: 16px; }
  .label { color: var(--ink-muted); }
  .cell {
    position: absolute; right: 48px; top: 146px;
    font-family: "Arimo", sans-serif; font-size: 15px; color: var(--ink-soft);
  }
</style>
</head>
<body>
<main class="canvas">
  <section class="card card--front" aria-label="Card front">
    <p class="company-name">Quarrystone Development<br>Group, LLC</p>
  </section>

  <section class="card card--back" aria-label="Card back">
    <p class="company-name">Quarrystone Development<br>Group, LLC</p>
    <p class="cell"><span class="label">Cell:</span> (555) 318-2046</p>
    <div class="person">
      <p class="person__name">DANIEL HARTWELL</p>
      <p class="person__title">Director</p>
      <div class="details">
        <p class="details__group"><span class="label">Address:</span> 1187 Fenwick<br>Ridge Salem, OR 97302</p>
        <p class="details__group"><span class="label">Email:</span> info@quarrystonegroup.com<br><span class="label">Web:</span> www.quarrystonegroup.com</p>
      </div>
    </div>
  </section>
</main>
</body>
</html>
```